Informational Site for Advanced Chemistry R&D

The company develops oxidation chemistry for air, water, fuel pollution controls. The site has been prototyped at www.velquaresearch.example. Take a look. Now, the task is to design it for eye-catching beauty with use of color, on-page scroll-driven color transition and parallax effects. Should capture the themes: high technology, wow it's beautiful, modern, uncluttered, clean urban environment.

Target Market(s)

China Environmentally Conscious Government and Industry,

Industry/Entity Type

It Company

Number of Pages Required

3 page

Font styles to use
Sans Serif

Requirements
Must have
• Parallax effects, desktop compatible, Rich, Modern, Simple, Graphic
Nice to have
• Mobile Phone Compatible
Should not have
• Flash, or anything that is slow to load or requires high bandwidth

```html
<!DOCTYPE html>
<html lang="en">
<head>
<meta charset="utf-8">
<title>Velqua — Advanced Oxidation</title>
<link rel="stylesheet" href="https://fonts.googleapis.com/css2?family=Roboto:wght@300;400;500;700&family=Roboto+Condensed:wght@400;700&display=swap">
<style>
:root{
  --teal:#27b8b3;
  --teal-dark:#1d9e9a;
  --blue:#1f6db5;
  --ink:#2b2b2b;
  --muted:#8a8a8a;
  --rule:#cfcfcf;
  --band:#f3f3f3;
  --footer:#ececec;
  --green:#3ccb3f;
  --gold:#e2a621;
  --magenta:#d6237b;
  --white:#ffffff;
}
*{box-sizing:border-box;margin:0;padding:0}
html,body{width:1200px;height:4054px;overflow:hidden;background:var(--white)}
body{font-family:"Roboto",Arial,sans-serif;color:var(--ink);position:relative}
.abs{position:absolute}
.heading{font-family:"Roboto Condensed","Arial Narrow",sans-serif;font-weight:700;font-size:26px;letter-spacing:.3px;text-align:center;width:1200px;left:0;color:var(--ink)}
.divider{left:100px;width:1000px;height:2px;background:var(--rule)}
.divider-dot{left:584px;width:32px;height:32px;border-radius:50%;background:var(--white);border:4px solid var(--teal)}
.btn{display:inline-block;background:var(--teal);color:var(--white);font-size:12px;font-weight:500;border-radius:4px;text-align:center;line-height:40px;height:40px;width:106px}
.photo{border-radius:2px}

/* hero */
.hero{left:0;top:0;width:1200px;height:676px;overflow:hidden}
.hero-photo{position:absolute;inset:0;background:linear-gradient(180deg,#2a3a4d 0%,#54718c 30%,#9d8e73 52%,#6f6550 64%,#3d5e74 78%,#6d8ea4 100%)}
.hero-veil{position:absolute;inset:0;background:linear-gradient(180deg,rgba(0,0,0,.25),rgba(0,0,0,0) 40%,rgba(0,0,0,.15))}
.brand{left:96px;top:60px;font-family:"Roboto",sans-serif;font-weight:500;font-size:30px;color:var(--white);display:flex;align-items:center;gap:12px}
.brand-dot{width:26px;height:26px;border-radius:50%;background:var(--teal)}
.nav{top:70px;right:100px;display:flex;gap:56px;font-size:13px;font-weight:500;color:var(--white)}
.nav .active{color:var(--teal)}
.hero-title{top:470px;left:0;width:1200px;text-align:center;color:var(--white);font-family:"Roboto Condensed",sans-serif;font-weight:700;font-size:48px;letter-spacing:.5px}
.hero-sub{top:535px;left:0;width:1200px;text-align:center;color:var(--white);font-family:"Roboto Condensed",sans-serif;font-weight:700;font-size:31px}
.slide-arrow{top:326px;width:40px;height:40px;border-radius:50%;background:rgba(255,255,255,.25);display:flex;align-items:center;justify-content:center}

/* ideas */
.ideas-name{left:100px;top:858px;color:var(--teal);font-weight:500;font-size:28px}
.ideas-list{left:100px;top:902px;list-style:none;font-size:14px;color:#555;text-transform:uppercase}
.ideas-list li{height:24px;display:flex;align-items:center;gap:12px}
.ideas-mark{left:380px;top:870px;width:240px;height:140px;display:flex;align-items:center;justify-content:center;gap:14px;font-weight:500;font-size:34px;color:var(--blue)}
.ideas-mark span.circle{width:30px;height:30px;border-radius:50%;background:var(--teal)}
.solutions-label{left:718px;top:858px;font-size:22px;font-weight:500;color:var(--ink)}
.solution-icon{width:86px;height:86px;border-radius:50%;background:var(--blue);display:flex;align-items:center;justify-content:center}
.solution-name{width:86px;text-align:center;font-size:16px;font-weight:500;top:1010px}

/* oxidation */
.oxidation{left:0;top:1108px;width:1200px;height:554px;background:var(--band)}
.ox-title{left:100px;top:1244px;font-size:25px;font-weight:500;color:var(--ink)}
.ox-text{left:100px;width:500px;font-size:12.5px;line-height:20px;color:#777}
.ox-point{left:100px;font-size:15px;color:#333;display:flex;align-items:center;gap:12px}
.ox-diagram{left:648px;top:1170px;width:500px;height:440px;border-radius:6px;background:radial-gradient(circle at 50% 48%,#f6d94a 0 9%,#fbf1c2 10% 40%,#f3f3f3 70%)}

/* solutions */
.sol-title{font-size:20px;font-weight:500;color:var(--ink)}
.sol-text{font-size:12.5px;line-height:20px;color:#777;width:480px}

/* partners */
.partners{left:0;top:3033px;width:1200px;height:378px;background:var(--band)}
.partner-badge{width:130px;height:110px}
.partner-btn{height:62px;border-radius:4px;color:var(--white);font-size:12px;font-weight:500;text-align:center;display:flex;align-items:center;justify-content:center;line-height:17px;top:3290px}

/* contact */
.contact-row{left:100px;display:flex;align-items:center;gap:22px;font-size:12.5px;color:#333}
.contact-icon{width:54px;height:54px;border-radius:50%;border:2px solid #555;display:flex;align-items:center;justify-content:center}
.social{top:3838px;width:30px;height:30px;border-radius:4px;background:#333}
.form{left:600px;top:3587px;width:500px;height:305px;background:var(--teal)}
.field{left:636px;width:424px;border:1px solid rgba(255,255,255,.6);color:rgba(255,255,255,.85);font-size:12px;padding:0 20px;display:flex;align-items:center}
.send{left:970px;top:3836px;width:64px;height:32px;background:#24282b;color:var(--white);font-size:12px;border-radius:3px;display:flex;align-items:center;justify-content:center}

.footer{left:0;top:3952px;width:1200px;height:102px;background:var(--footer);font-size:12px;color:#777}
</style>
</head>
<body>

<!-- hero -->
<header class="abs hero">
  <div class="hero-photo" role="img" aria-label="Coastal city skyline at dusk with towers beside a beach and sea"></div>
  <div class="hero-veil"></div>
  <div class="abs brand"><span class="brand-dot"></span>Velqua</div>
  <nav class="abs nav"><span class="active">HOME</span><span>TECHNOLOGY</span><span>PRODUCTS</span><span>CONTACT</span></nav>
  <div class="abs slide-arrow" style="left:60px"><svg width="14" height="14" viewBox="0 0 14 14"><path d="M9 2 4 7l5 5" fill="none" stroke="#fff" stroke-width="2"/></svg></div>
  <div class="abs slide-arrow" style="right:60px"><svg width="14" height="14" viewBox="0 0 14 14"><path d="M5 2l5 5-5 5" fill="none" stroke="#fff" stroke-width="2"/></svg></div>
  <h1 class="abs hero-title">ADVANCED OXIDATION</h1>
  <p class="abs hero-sub">Science for Environmental Pollution Management</p>
  <svg class="abs" style="left:0;top:560px" width="1200" height="116" viewBox="0 0 1200 116" preserveAspectRatio="none">
    <path d="M0 40 C300 140 520 120 760 70 C950 30 1080 20 1200 30 L1200 116 L0 116Z" fill="#1e8fa6" opacity=".9"/>
    <path d="M0 62 C300 150 540 130 780 84 C960 50 1090 44 1200 52 L1200 116 L0 116Z" fill="#ffffff"/>
  </svg>
</header>

<!-- ideas -->
<section>
  <h2 class="abs heading" style="top:766px">NEW IDEAS FOR A CLEANER WORLD</h2>
  <div class="abs divider" style="top:818px"></div>
  <div class="abs divider-dot" style="top:803px"></div>
  <div class="abs ideas-name">Velqua</div>
  <ul class="abs ideas-list">
    <li><svg width="16" height="12" viewBox="0 0 16 12"><path d="M1 11C3 5 7 3 12 3M9 0l4 3-4 3" fill="none" stroke="#27b8b3" stroke-width="2"/></svg>Environmental</li>
    <li><svg width="16" height="12" viewBox="0 0 16 12"><path d="M1 11C3 5 7 3 12 3M9 0l4 3-4 3" fill="none" stroke="#27b8b3" stroke-width="2"/></svg>Pollution control</li>
    <li><svg width="16" height="12" viewBox="0 0 16 12"><path d="M1 11C3 5 7 3 12 3M9 0l4 3-4 3" fill="none" stroke="#27b8b3" stroke-width="2"/></svg>Solutions employing</li>
    <li><svg width="16" height="12" viewBox="0 0 16 12"><path d="M1 11C3 5 7 3 12 3M9 0l4 3-4 3" fill="none" stroke="#27b8b3" stroke-width="2"/></svg>Nature's most</li>
    <li><svg width="16" height="12" viewBox="0 0 16 12"><path d="M1 11C3 5 7 3 12 3M9 0l4 3-4 3" fill="none" stroke="#27b8b3" stroke-width="2"/></svg>Reactive free</li>
    <li><svg width="16" height="12" viewBox="0 0 16 12"><path d="M1 11C3 5 7 3 12 3M9 0l4 3-4 3" fill="none" stroke="#27b8b3" stroke-width="2"/></svg>Radical</li>
  </ul>
  <div class="abs ideas-mark"><span class="circle"></span>Velqua</div>
  <div class="abs solutions-label">SOLUTIONS</div>
  <div class="abs solution-icon" style="left:718px;top:908px"><svg width="30" height="36" viewBox="0 0 30 36"><path d="M15 2C10 12 4 18 4 24a11 11 0 0 0 22 0C26 18 20 12 15 2Z" fill="#fff"/></svg></div>
  <div class="abs solution-icon" style="left:866px;top:908px"><svg width="36" height="30" viewBox="0 0 36 30"><path d="M2 10h22a5 5 0 1 0-5-5M2 17h28a4 4 0 1 1-4 4M2 24h14" fill="none" stroke="#fff" stroke-width="3" stroke-linecap="round"/></svg></div>
  <div class="abs solution-icon" style="left:1014px;top:908px"><svg width="28" height="34" viewBox="0 0 28 34"><path d="M6 2h11l7 7v21a2 2 0 0 1-2 2H6a2 2 0 0 1-2-2V4a2 2 0 0 1 2-2Z" fill="#fff"/><path d="M14 14c-3 4-4 6-4 8a4 4 0 0 0 8 0c0-2-1-4-4-8Z" fill="#1f6db5"/></svg></div>
  <div class="abs solution-name" style="left:718px">WATER</div>
  <div class="abs solution-name" style="left:866px">AIR</div>
  <div class="abs solution-name" style="left:1014px">FUEL</div>
</section>

<!-- oxidation -->
<section class="abs oxidation"></section>
<h2 class="abs ox-title">ADVANCED OXIDATION</h2>
<p class="abs ox-text" style="top:1284px">Advanced Oxidation refers to a variety of techniques employing the Hydroxyl Radical, an energetic, highly reactive cousin of the water molecule:</p>
<div class="abs ox-point" style="top:1338px"><svg width="16" height="16"><circle cx="8" cy="8" r="6" fill="none" stroke="#333" stroke-width="2"/><circle cx="8" cy="8" r="2" fill="#333"/></svg>To add oxygen to inorganic molecules</div>
<div class="abs ox-point" style="top:1368px"><svg width="16" height="16"><circle cx="8" cy="8" r="6" fill="none" stroke="#333" stroke-width="2"/><circle cx="8" cy="8" r="2" fill="#333"/></svg>To remove hydrogen from organic molecules</div>
<p class="abs ox-text" style="top:1420px">These transformations convert important industrial contaminants into reactive forms that can be captured or that disintegrate into harmless end products.</p>
<a class="abs btn" style="left:100px;top:1490px">READ MORE</a>
<div class="abs ox-diagram" role="img" aria-label="Diagram of the hydroxyl radical reacting with pollutant molecules such as NO, SO2, CO and H2S"></div>

<!-- solutions -->
<section>
  <h2 class="abs heading" style="top:1724px">OUR SOLUTIONS</h2>
  <div class="abs divider" style="top:1784px"></div>
  <div class="abs divider-dot" style="top:1769px"></div>

  <h3 class="abs sol-title" style="left:100px;top:1890px">Fuel Oil Desulfurization</h3>
  <p class="abs sol-text" style="left:100px;top:1930px">Our proprietary low temperature and pressure advanced oxidation catalytic process reliably removes sulfur from diesel transportation fuel at less than half the operating costs of older hydro-desulfurization processes.</p>
  <a class="abs btn" style="left:100px;top:2010px">READ MORE</a>
  <div class="abs photo" style="left:600px;top:1833px;width:497px;height:278px;background:linear-gradient(160deg,#5d6f7e,#2f3c46 60%,#1d262d)" role="img" aria-label="Industrial refinery towers and pipework"></div>

  <div class="abs photo" style="left:103px;top:2119px;width:492px;height:279px;background:linear-gradient(150deg,#6f8aa0,#2d4f76 55%,#1b3558)" role="img" aria-label="Worker handling blue chemical drums"></div>
  <h3 class="abs sol-title" style="left:648px;top:2176px">Volatile Organic Compunds (VOC)</h3>
  <p class="abs sol-text" style="left:648px;top:2214px">Alkenes, alkenes, halogenated hydrocarbons, aromatic hydrocarbons, esters, aldehydes, polycyclic aromatic hydrocarbons. We convert these by-products of industrial processes before they enter the atmosphere and cause smog.</p>
  <a class="abs btn" style="left:648px;top:2298px">READ MORE</a>

  <h3 class="abs sol-title" style="left:100px;top:2462px">Flue Gas Scrubbing</h3>
  <p class="abs sol-text" style="left:100px;top:2500px">Desulfurization and denitrification using our proprietary flue gas advanced oxidation catalytic process (FGASC). Sulfur and nitrogen are oxidized and adsorbed into an environmentally friendly solid medium for safe removal from site.</p>
  <a class="abs btn" style="left:100px;top:2586px">READ MORE</a>
  <div class="abs photo" style="left:600px;top:2406px;width:497px;height:278px;background:linear-gradient(180deg,#8a95a6,#4d586c 55%,#1f2634)" role="img" aria-label="Smokestacks releasing flue gas against a grey sky"></div>

  <div class="abs photo" style="left:103px;top:2690px;width:492px;height:278px;background:linear-gradient(170deg,#7f8d55,#5f6b3e 40%,#9c8a6a 70%,#b8a98c)" role="img" aria-label="Wastewater outflow pipe discharging into a stream"></div>
  <h3 class="abs sol-title" style="left:648px;top:2744px">Wastewater Treatment</h3>
  <p class="abs sol-text" style="left:648px;top:2782px">Photoelectrocatalyzed (PEC) anodic oxidation removes soluble organics. Novel anode design using our proprietary nano-carbon surface operates non-selectively to remove 99% of contaminants across a wide range of chemical oxygen demand.</p>
  <a class="abs btn" style="left:648px;top:2866px">READ MORE</a>
</section>

<!-- partners -->
<section class="abs partners"></section>
<h2 class="abs heading" style="top:3076px">OUR PARTNERS</h2>
<div class="abs divider" style="top:3134px"></div>
<div class="abs divider-dot" style="top:3119px"></div>
<div class="abs" style="left:120px;top:3198px;display:flex;align-items:center;gap:10px;color:var(--blue);font-weight:500;font-size:22px"><span style="width:18px;height:18px;border-radius:50%;background:var(--teal)"></span>Velqua Systems</div>
<div class="abs partner-badge" style="left:398px;top:3166px;border-radius:50%;width:110px;background:#e03a2a"></div>
<div class="abs partner-badge" style="left:681px;top:3166px;border-radius:50%;width:110px;background:#26547f"></div>
<div class="abs partner-badge" style="left:952px;top:3166px;border-radius:50%;width:110px;background:#c3243a"></div>
<div class="abs partner-btn" style="left:100px;width:230px;background:var(--green)">OUR SALES PARTNER<br>IN CHINA</div>
<div class="abs partner-btn" style="left:370px;width:187px;background:var(--teal)">CONSTRUCTION PARTNER<br>IN CHINA</div>
<div class="abs partner-btn" style="left:643px;width:187px;background:var(--gold)">TECHNOLOGY PARTNER<br>IN CHINA</div>
<div class="abs partner-btn" style="left:914px;width:186px;background:var(--magenta)">TECHNOLOGY PARTNER<br>IN CHINA</div>

<!-- contact -->
<section>
  <h2 class="abs heading" style="top:3452px">OUR CONTACT</h2>
  <div class="abs divider" style="top:3510px"></div>
  <div class="abs divider-dot" style="top:3495px"></div>
  <div class="abs contact-row" style="top:3584px"><span class="contact-icon"><svg width="16" height="22" viewBox="0 0 16 22"><path d="M8 1a7 7 0 0 0-7 7c0 5 7 13 7 13s7-8 7-13a7 7 0 0 0-7-7Z" fill="#333"/><circle cx="8" cy="8" r="2.5" fill="#fff"/></svg></span>Velqua Research Corporation, Harlow Bay, U.S.A.</div>
  <div class="abs contact-row" style="top:3663px"><span class="contact-icon"><svg width="20" height="14" viewBox="0 0 20 14"><rect width="20" height="14" rx="2" fill="#333"/><path d="M1 1l9 7 9-7" fill="none" stroke="#fff" stroke-width="1.5"/></svg></span>info@velquaresearch.example</div>
  <div class="abs contact-row" style="top:3738px"><span class="contact-icon"><svg width="18" height="18" viewBox="0 0 18 18"><path d="M4 1l3 4-2 2c1 2 4 5 6 6l2-2 4 3-2 3C8 17 1 10 1 3Z" fill="#333"/></svg></span>+1 555 014 2290</div>
  <span class="abs social" style="left:100px"></span>
  <span class="abs social" style="left:150px"></span>
  <span class="abs social" style="left:200px"></span>
  <span class="abs social" style="left:250px"></span>
  <span class="abs social" style="left:300px"></span>

  <div class="abs form"></div>
  <div class="abs field" style="top:3610px;height:64px">Your Email *</div>
  <div class="abs field" style="top:3692px;height:64px">Your Password *</div>
  <div class="abs field" style="top:3774px;height:80px;align-items:flex-start;padding-top:20px">Your Message *</div>
  <div class="abs send">SEND</div>
</section>

<footer class="abs footer">
  <div class="abs" style="left:0;width:1200px;top:42px;text-align:center">© Copy Rights 2016 – velquaresearch.example – all rights reserved</div>
  <div class="abs" style="right:100px;top:42px">C.16</div>
</footer>

</body>
</html>
```